Lanternfield Drinks business cards

We need a business card design for our new logo. The company is modern, progressive, professional, yet approachable. The key products are ready to drink bottles and cans of coffee based beverages.
These cards will be a critical part of the first impression made by our sales organization, business development team, and all external facing personnel.
Card can be a vertical or horizontal orientation.

Target Market(s)

Customers, suppliers, business partners

Industry/Entity Type

Business

Contact Information for Business Card

Business cards should feature Company Name and Logo.

Font styles to use
Serif

Colors

Designer to choose colors to be used in the design.

Requirements
Must have
• Strong readability of Name, phone #, mobile number and email address.
• Job title, website url, Street Address, and other details can be secondary level readability.
Nice to have
• High impact, simplistic quality design.
• Ok to utilize the 'H in the box' separate from the company name

```html
<!DOCTYPE html>
<html lang="en">
<head>
<meta charset="utf-8">
<title>Lanternfield Drinks business cards</title>
<link rel="stylesheet" href="https://fonts.googleapis.com/css2?family=Crimson+Pro:ital,wght@0,400;0,600;0,700;1,400&display=swap">
<style>
  :root {
    --backdrop: #3b3b3c;
    --card: #1e1e1f;
    --orange: #e2552a;
    --amber: #ef9a2a;
    --ink-light: #f1eee9;
  }
  * { box-sizing: border-box; margin: 0; padding: 0; }
  html, body { width: 799px; height: 1200px; overflow: hidden; }
  body {
    background: var(--backdrop);
    font-family: "Crimson Pro", Georgia, serif;
    position: relative;
  }
  .card {
    position: absolute;
    left: 60px;
    width: 680px;
    height: 388px;
    background: var(--card);
    border-radius: 4px;
    box-shadow: 0 14px 30px rgba(0,0,0,.45);
    overflow: hidden;
  }
  .card--front { top: 100px; }
  .card--back { top: 712px; }

  .brand {
    display: flex;
    align-items: center;
    gap: 14px;
  }
  .brand__square {
    width: 54px; height: 54px;
    border: 4px solid var(--orange);
  }
  .brand__name {
    color: var(--orange);
    font-weight: 700;
    font-size: 40px;
    letter-spacing: 1px;
    text-transform: uppercase;
    line-height: 1;
  }

  /* front */
  .card--front .brand {
    position: absolute;
    top: 130px; left: 0; right: 0;
    justify-content: center;
  }
  .front-url {
    position: absolute;
    top: 262px; left: 0; right: 0;
    display: flex;
    align-items: center;
    justify-content: center;
    gap: 16px;
    font-size: 21px;
    color: var(--ink-light);
    letter-spacing: .5px;
  }
  .front-url__accent { color: var(--amber); }
  .front-url__dash {
    width: 52px; height: 4px;
    background: var(--orange);
    clip-path: polygon(0 0, 100% 50%, 0 100%);
  }
  .front-url__dash--left { clip-path: polygon(0 50%, 100% 0, 100% 100%); }

  /* back */
  .card--back .brand {
    position: absolute;
    top: 30px; left: 34px;
  }
  .card--back .brand__name { font-size: 36px; }
  .person {
    position: absolute;
    top: 112px; left: 40px;
  }
  .person__name {
    color: var(--orange);
    font-weight: 600;
    font-size: 27px;
    line-height: 1;
  }
  .person__title {
    color: var(--ink-light);
    font-style: italic;
    font-size: 16px;
    margin-top: 4px;
  }
  .rule {
    position: absolute;
    top: 150px; left: 252px; right: 36px;
    height: 2px;
    background: var(--amber);
  }
  .contacts {
    position: absolute;
    top: 180px; left: 40px;
    list-style: none;
    color: var(--ink-light);
    font-size: 18px;
    line-height: 26px;
  }
  .contacts li { display: flex; align-items: center; gap: 12px; }
  .contacts svg { width: 15px; height: 15px; fill: var(--orange); flex: none; }
  .address {
    position: absolute;
    right: 40px; bottom: 46px;
    text-align: right;
    color: var(--ink-light);
    font-size: 19px;
    line-height: 24px;
  }
  .base-band {
    position: absolute;
    left: 0; right: 0; bottom: 0;
    height: 14px;
    background: linear-gradient(90deg, var(--orange) 0%, var(--orange) 70%, var(--amber) 100%);
  }
</style>
</head>
<body>

<section class="card card--front">
  <div class="brand">
    <span class="brand__square"></span>
    <span class="brand__name">Lanternfield Drinks</span>
  </div>
  <div class="front-url">
    <span class="front-url__dash front-url__dash--left"></span>
    <span>www.<span class="front-url__accent">lanternfielddrinks</span>.com</span>
    <span class="front-url__dash"></span>
  </div>
</section>

<section class="card card--back">
  <div class="brand">
    <span class="brand__square"></span>
    <span class="brand__name">Lanternfield Drinks</span>
  </div>

  <div class="person">
    <p class="person__name">John Doe Smith</p>
    <p class="person__title">Managing Director</p>
  </div>
  <div class="rule"></div>

  <ul class="contacts">
    <li>
      <svg viewBox="0 0 16 16" aria-hidden="true"><path d="M3 1l3 3-1.5 2a9 9 0 0 0 5.5 5.5L12 10l3 3-2 2C7 15 1 9 1 3z"/></svg>
      555.555.5555
    </li>
    <li>
      <svg viewBox="0 0 16 16" aria-hidden="true"><path d="M4 0h8a1 1 0 0 1 1 1v14a1 1 0 0 1-1 1H4a1 1 0 0 1-1-1V1a1 1 0 0 1 1-1zm1 2v10h6V2zm3 11a1 1 0 1 0 0 2 1 1 0 0 0 0-2z"/></svg>
      666.666.7777
    </li>
    <li>
      <svg viewBox="0 0 16 16" aria-hidden="true"><path d="M0 3h16v10H0zm1.5 1.2L8 9l6.5-4.8V4h-13z"/></svg>
      johndoe@yourwebsite.com
    </li>
    <li>
      <svg viewBox="0 0 16 16" aria-hidden="true"><path d="M8 0a8 8 0 1 0 0 16A8 8 0 0 0 8 0zm0 1.5c1 0 2 1.8 2.3 4.5H5.7C6 3.3 7 1.5 8 1.5zM1.6 7h3.9v2H1.6zm8.9 0h3.9v2h-3.9zM6.5 7h3v2h-3zm-.8 3h4.6C10 12.7 9 14.5 8 14.5S6 12.7 5.7 10z"/></svg>
      www.yourwebsite.com
    </li>
  </ul>

  <address class="address" style="font-style:normal">
    234 Anywhere St.,<br>
    Any Town, US 123456
  </address>

  <div class="base-band"></div>
</section>

</body>
</html>
```